Business Card Design for company

We want new business cards. We'd like something different-- yet still highly professional. Our tagline is Providing leadership, delivering success. Stock photos are ok, as long as they are relevant and look upscale.

Target Market(s)

Architecture/Business Management Consulting/Engineering Consulting

Contact Information for Business Card

dark gray background with pops of blue might be good, but you tell me. You're the designers. Rounded corners might be nice, but again, you tell me.

Font styles to use
Serif
Sans Serif

Colors
3276b5
5c5c5c
9d9d9d
fbfbfb

Requirements
Nice to have
• Something different, but still very professional.

```html
<!DOCTYPE html>
<html lang="en">
<head>
<meta charset="utf-8">
<title>Talven Partners – Business Card</title>
<link rel="stylesheet" href="https://fonts.googleapis.com/css2?family=Montserrat:wght@600;700&family=Roboto:wght@400;500;700&display=swap">
<style>
  :root {
    --brand-blue: #2c66a3;
    --accent-blue: #3276b5;
    --panel-gray: #4a4d52;
    --mid-gray: #5c5c5c;
    --soft-gray: #9d9d9d;
    --paper: #fbfbfb;
    --page: #e6e7e9;
  }
  * { margin: 0; padding: 0; box-sizing: border-box; }
  html, body {
    width: 1200px; height: 1108px; overflow: hidden;
    background: var(--page);
    font-family: "Roboto", Arial, sans-serif;
  }
  .stage {
    width: 1200px; height: 1108px;
    display: flex; flex-direction: column; align-items: center;
    justify-content: center; gap: 36px;
  }
  .card {
    position: relative;
    width: 875px; height: 500px;
    border-radius: 14px;
    overflow: hidden;
    box-shadow: 0 6px 18px rgba(0,0,0,0.18);
  }
  /* Front */
  .card-front {
    background: var(--brand-blue);
    color: var(--paper);
  }
  .front-wordmark {
    position: absolute; left: 0; right: 0; top: 160px;
    text-align: center;
    font-family: "Montserrat", Arial, sans-serif;
    font-weight: 700; font-size: 104px; letter-spacing: 4px;
    line-height: 1;
  }
  .front-tagline {
    position: absolute; left: 0; right: 0; top: 330px;
    text-align: center;
    font-size: 22px; letter-spacing: 0.5px;
  }
  .front-tagline .dot { margin: 0 10px; }
  /* Back */
  .card-back { background: var(--paper); }
  .back-shapes { position: absolute; inset: 0; }
  .contact {
    position: absolute; left: 52px; top: 56px;
    color: var(--paper);
  }
  .contact-name {
    font-weight: 700; font-size: 30px; letter-spacing: 1px;
    text-transform: uppercase;
  }
  .contact-title {
    font-size: 18px; text-transform: uppercase; letter-spacing: 0.5px;
    margin-top: 4px;
  }
  .contact-address {
    font-size: 18px; line-height: 1.35; margin-top: 30px;
  }
  .contact-list { list-style: none; margin-top: 14px; }
  .contact-list li {
    display: flex; align-items: center; gap: 12px;
    font-size: 18px; line-height: 1.6;
  }
  .contact-list svg { width: 16px; height: 16px; flex: none; }
  .back-wordmark {
    position: absolute; left: 450px; right: 20px; top: 190px;
    text-align: center;
    font-family: "Montserrat", Arial, sans-serif;
    font-weight: 700; color: var(--brand-blue);
    line-height: 1.05;
  }
  .back-wordmark .big { display: block; font-size: 78px; letter-spacing: 4px; }
  .back-wordmark .small { display: block; font-size: 30px; letter-spacing: 9px; margin-top: 6px; }
</style>
</head>
<body>
<main class="stage">
  <section class="card card-front" aria-label="Card front">
    <div class="front-wordmark">TALVEN</div>
    <p class="front-tagline">Providing leadership<span class="dot">•</span>delivering success</p>
  </section>

  <section class="card card-back" aria-label="Card back">
    <svg class="back-shapes" viewBox="0 0 875 500" width="875" height="500" aria-hidden="true">
      <polygon points="0,0 650,0 420,220 380,500 0,500" fill="var(--panel-gray)"/>
      <polyline points="676,0 440,226 400,500" fill="none" stroke="var(--accent-blue)" stroke-width="6"/>
    </svg>

    <div class="contact">
      <h1 class="contact-name">Daniel Reeve</h1>
      <p class="contact-title">CEO/Founder</p>
      <p class="contact-address">412 Harbor View Road<br>Juneau, Alaska 99801</p>
      <ul class="contact-list">
        <li>
          <svg viewBox="0 0 16 16" fill="currentColor"><path d="M3.5 1.5l2.5 0 1 3.5-1.6 1.2a8 8 0 0 0 4.4 4.4L11 9l3.5 1v2.5c0 1-1 2-2 2C6.5 14.5 1.5 9.5 1.5 3.5c0-1 1-2 2-2z"/></svg>
          <span>555 210 4417</span>
        </li>
        <li>
          <svg viewBox="0 0 16 16" fill="none" stroke="currentColor" stroke-width="1.6"><rect x="4" y="1" width="8" height="14" rx="1.5"/><line x1="7" y1="12.5" x2="9" y2="12.5"/></svg>
          <span>555 318 2290</span>
        </li>
        <li>
          <svg viewBox="0 0 16 16" fill="currentColor"><rect x="4" y="1.5" width="8" height="4"/><rect x="1" y="6" width="14" height="6" rx="1"/><rect x="4" y="10" width="8" height="4.5"/></svg>
          <span>555 604 7731</span>
        </li>
        <li>
          <svg viewBox="0 0 16 16" fill="none" stroke="currentColor" stroke-width="1.6"><rect x="1" y="3" width="14" height="10" rx="1"/><polyline points="1.5,3.5 8,9 14.5,3.5"/></svg>
          <span>daniel@talvenpartners.com</span>
        </li>
        <li>
          <svg viewBox="0 0 16 16" fill="none" stroke="currentColor" stroke-width="1.4"><circle cx="8" cy="8" r="6.5"/><ellipse cx="8" cy="8" rx="2.8" ry="6.5"/><line x1="1.5" y1="8" x2="14.5" y2="8"/></svg>
          <span>www.talvenpartners.com</span>
        </li>
      </ul>
    </div>

    <div class="back-wordmark">
      <span class="big">TALVEN</span>
      <span class="small">PARTNERS</span>
    </div>
  </section>
</main>
</body>
</html>
```